Navoro & Omvar Automotive Repair Shop. Need a new website design.

We specialize in Navoro & Omvar auto repair, but also work on other Asian import vehicles. We have been in business for 7 years and pride ourselves on high quality auto repair that is fixed right the first time. Would like the automotive repair website to incorporate the colors black, red and white if possible and have our logo and some Navoro and Omvar vehicles included in the website.

Target Market(s)

Navoro & Omvar vehicle owners

Industry/Entity Type

Automotive Repair

Coding

Coded - Design and coding required

Number of Pages Required

5+ page

Colors
EB3D1F
EC4F4E
F09395
F8D3D4
FCEDEE

Requirements
Must have
• Home, Services, Contact Us, Schedule appointment, and a gallery tab that I can add shop pictures to when completed.
Nice to have
• Would like to see example pictures of job next to each service listed.
Should not have
• Service not related to auto repair. Ex. auto detailing, towing, car wash

```html
<!DOCTYPE html>
<html lang="en">
<head>
<meta charset="utf-8">
<title>Corvan Automotive — Navoro &amp; Omvar Auto Repair</title>
<link href="https://fonts.googleapis.com/css2?family=Orbitron:wght@700;800;900&family=Roboto:wght@400;500;700&display=swap" rel="stylesheet">
<style>
:root{
  --red:#e3141b;
  --red-deep:#b30d12;
  --black:#050505;
  --ink:#0d0d0d;
  --panel:#1b1b1b;
  --gray:#2e2e2e;
  --line:#4a4a4a;
  --steel:#8a8a8a;
  --white:#ffffff;
  --soft:#d6d6d6;
  --head:'Orbitron', sans-serif;
  --body:'Roboto', sans-serif;
}
*{box-sizing:border-box;margin:0;padding:0}
html,body{width:1200px;height:4612px;overflow:hidden}
body{position:relative;background:var(--black);color:var(--white);font-family:var(--body)}
.abs{position:absolute}
.head{font-family:var(--head);font-weight:900;letter-spacing:1px;text-transform:uppercase}
.eyebrow{font-family:var(--body);font-size:14px;letter-spacing:1px;color:var(--red);text-transform:uppercase}
.btn{position:absolute;display:flex;align-items:center;justify-content:center;gap:8px;background:var(--red);color:var(--white);font-weight:700;font-size:15px;text-transform:uppercase;letter-spacing:.3px;white-space:nowrap}
.photo{position:absolute}

/* header + hero */
.hero{position:absolute;left:0;top:0;width:1200px;height:790px;background:linear-gradient(90deg,#050505 0%,#0b0b0b 38%,#1d1d1d 100%)}
.hero-photo{left:480px;top:0;width:720px;height:700px;
  background:
    linear-gradient(90deg,#0b0b0b 0%,rgba(11,11,11,.6) 16%,rgba(11,11,11,0) 34%),
    radial-gradient(ellipse 120px 90px at 560px 470px,rgba(200,30,30,.75),rgba(200,30,30,0)),
    radial-gradient(ellipse 130px 110px at 660px 330px,rgba(205,170,150,.8),rgba(205,170,150,0)),
    radial-gradient(ellipse 300px 230px at 370px 360px,#d9dadc 0%,#a9abae 30%,rgba(90,92,96,.6) 60%,rgba(30,30,31,0) 85%),
    radial-gradient(ellipse 260px 200px at 420px 120px,#7c7e80,rgba(40,40,42,0)),
    linear-gradient(160deg,#3a3a3c 0%,#1c1c1d 60%,#0c0c0c 100%)}
.brand{position:absolute;display:flex;align-items:center;gap:10px;font-family:var(--body);font-weight:700;color:var(--white);text-transform:uppercase}
.brand .dot{width:18px;height:18px;border-radius:50%;background:var(--red)}
.nav{position:absolute;top:44px;left:367px;display:flex;font-size:13px;font-weight:500;text-transform:uppercase}
.nav a{color:var(--white);text-decoration:none;position:absolute;white-space:nowrap}
.nav a.active{border-bottom:2px solid var(--red);padding-bottom:8px}
.nav .sep{position:absolute;color:#888}
.finance{position:absolute;left:917px;top:39px;width:188px;height:40px;border:1px solid var(--red);color:var(--red);font-size:12px;display:flex;align-items:center;justify-content:center;text-transform:uppercase}
.hero-frame{left:125px;top:229px;width:131px;height:366px;border:4px solid #4d4d4d;border-right:none}
.hero-title{left:172px;top:272px;font-size:31px;line-height:41px;white-space:nowrap}
.hero-title .red{color:var(--red)}
.hero-copy{left:174px;top:402px;width:390px;font-size:16px;line-height:21px}

/* about */
.about-accent{left:104px;top:842px;width:60px;height:90px;background:var(--red)}
.about-photo{left:113px;top:853px;width:448px;height:401px;
  background:
    radial-gradient(ellipse 80px 90px at 140px 300px,rgba(35,60,110,.95),rgba(35,60,110,0)),
    radial-gradient(ellipse 90px 80px at 210px 150px,#2a2a2a,rgba(42,42,42,0)),
    radial-gradient(ellipse 120px 40px at 330px 110px,rgba(170,120,70,.8),rgba(170,120,70,0)),
    radial-gradient(ellipse 200px 60px at 224px 30px,#b9b7b0,rgba(150,148,140,0)),
    radial-gradient(ellipse 70px 80px at 390px 340px,rgba(190,40,40,.6),rgba(190,40,40,0)),
    linear-gradient(170deg,#8a8983 0%,#5a5954 40%,#35342f 75%,#1e1e1e 100%)}
.engine-art{left:60px;top:1075px;width:262px;height:242px;background:radial-gradient(ellipse at 50% 50%,rgba(225,225,225,.85) 0%,rgba(140,140,140,.55) 35%,rgba(5,5,5,0) 70%)}
.years{left:460px;top:1166px;width:122px;height:113px;background:var(--red);text-align:center;padding-top:12px}
.years b{display:block;font-family:var(--head);font-size:34px;font-weight:900;line-height:36px}
.years span{font-size:14px;line-height:17px;text-transform:uppercase}
.about-side{left:564px;top:920px;width:4px;height:62px;background:#444}
.about-title{left:609px;top:876px;font-size:34px}
.about-mark{left:966px;top:890px;width:10px;height:10px;background:var(--red)}
.lead{left:613px;top:933px;width:520px;font-size:15.5px;font-weight:700;line-height:23px}
.about-copy{left:613px;top:1018px;width:520px;font-size:14px;line-height:23px;color:var(--soft)}
.outline-btn{position:absolute;left:620px;top:1230px;width:165px;height:46px;border:2px solid var(--red);color:var(--red);font-size:13px;letter-spacing:2px;display:flex;align-items:center;justify-content:center}

/* partners + services */
.services-bg{left:0;top:1540px;width:1200px;height:700px;background:linear-gradient(180deg,#2a2a2a 0%,#1c1c1c 40%,#181818 100%)}
.partners{left:111px;top:1361px;width:958px;height:256px;background:#101010;border:1px solid #3a3a3a}
.corner-tl{left:104px;top:1355px;width:95px;height:60px;border-top:5px solid #555;border-left:5px solid #555}
.corner-br{left:980px;top:1560px;width:95px;height:63px;border-bottom:5px solid #555;border-right:5px solid #555}
.partners-title{left:111px;top:1400px;width:958px;text-align:center;font-size:18px;line-height:24px;letter-spacing:1.5px}
.badge{position:absolute}
.svc-title{left:0;top:1714px;width:1200px;text-align:center;font-size:32px}
.svc-eyebrow{left:0;top:1684px;width:1200px;text-align:center}
.svc-hl{left:97px;top:1787px;width:285px;height:52px;background:var(--red);clip-path:polygon(0 0,100% 0,94% 100%,0 100%)}
.svc{position:absolute;display:flex;align-items:flex-start;gap:14px;font-size:15.5px;line-height:22px;white-space:nowrap}
.svc svg{flex:none;margin-top:-2px}

/* gallery */
.gallery-bg{left:0;top:2221px;width:1200px;height:880px;background:linear-gradient(180deg,#222 0%,#1a1a1a 50%,#0d0d0d 100%)}
.gal-eyebrow{left:0;top:2415px;width:1200px;text-align:center}
.gal-title{left:0;top:2446px;width:1200px;text-align:center;font-size:32px}

/* makes */
.makes-title{left:0;top:3160px;width:1200px;text-align:center;font-size:20px;line-height:25px;letter-spacing:1.5px}
.makes{left:131px;top:3283px;width:919px;height:287px;display:grid;grid-template-columns:repeat(4,1fr);grid-template-rows:repeat(2,1fr);border:1px solid var(--line)}
.make{border:1px solid var(--line);display:flex;flex-direction:column;align-items:center;justify-content:center;gap:10px;font-size:20px;font-weight:700;letter-spacing:2px;text-transform:uppercase;color:var(--soft)}
.make i{width:36px;height:36px;border:3px solid var(--soft);border-radius:50%}
.make.silver{background:linear-gradient(120deg,#8f8f8f,#e5e5e5 45%,#9c9c9c);color:#222}
.make.silver i{border-color:var(--red)}

/* contact */
.contact-bg{left:0;top:3752px;width:1200px;height:555px;background:linear-gradient(90deg,#161616,#1f1f1f 60%,#141414)}
.contact-line{left:54px;top:3953px;width:56px;height:3px;background:var(--red)}
.contact-eyebrow{left:135px;top:3896px}
.contact-title{left:135px;top:3928px;font-size:32px}
.contact-title span{color:var(--red)}
.contact-copy{left:135px;top:3989px;width:390px;font-size:14.5px;line-height:27px;color:var(--soft)}
.pay{position:absolute;left:140px;top:4166px;display:flex;align-items:center;gap:10px;font-size:26px;font-weight:700;color:#2fb45a}
.pay i{width:34px;height:34px;border-radius:50%;background:#2fb45a}
.form{left:591px;top:3838px;width:491px;height:451px;background:#2c2c2c}
.form-title{left:638px;top:3875px;font-size:17px;letter-spacing:1.5px}
.field{position:absolute;border:1px solid #8a8a8a;font-size:11px;padding:9px 14px;color:var(--soft)}

/* footer */
.footer-nav{position:absolute;top:4450px;left:0;width:1200px;font-size:16px;font-weight:700;text-transform:uppercase}
.footer-nav a{position:absolute;color:var(--white);text-decoration:none}
.footer-nav .dot{position:absolute;top:8px;width:5px;height:5px;border-radius:50%;background:var(--red)}
.copyright{left:0;top:4500px;width:1200px;text-align:center;font-size:12px;color:var(--soft)}
.social{position:absolute;top:4548px;left:0;width:1200px;display:flex;justify-content:center;gap:26px;font-size:13px;font-weight:500}
.social span:first-child{color:var(--red)}
</style>
</head>
<body>

<!-- HERO -->
<section class="hero">
  <div class="photo hero-photo" role="img" aria-label="Mechanic's hands working on an open engine block with camshafts"></div>
  <div class="brand" style="left:125px;top:60px;font-size:24px"><span class="dot"></span>Corvan</div>
  <nav class="nav">
    <a class="active" style="left:0">Home</a><span class="sep" style="left:56px">|</span>
    <a style="left:90px">About Us</a><span class="sep" style="left:174px">|</span>
    <a style="left:206px">Our Services</a><span class="sep" style="left:320px">|</span>
    <a style="left:351px">Gallery</a><span class="sep" style="left:422px">|</span>
    <a style="left:460px">Contact</a>
  </nav>
  <div class="finance">$ Financing Application</div>
  <div class="abs hero-frame"></div>
  <h1 class="abs head hero-title">Specializing in<br>Navoro and Omvar<br><span class="red">Auto Repair</span></h1>
  <p class="abs hero-copy">Corvan Automotive is a locally owned and operated auto repair shop in Brookfield that offers comprehensive car care and services</p>
  <div class="btn" style="left:174px;top:487px;width:299px;height:56px">Schedule an appointment
    <svg width="10" height="12" viewBox="0 0 10 12"><path d="M2 1l5 5-5 5" stroke="#fff" stroke-width="2.4" fill="none"/></svg></div>
</section>
<svg class="abs" style="left:0;top:640px" width="1200" height="150" viewBox="0 0 1200 150">
  <polygon points="0,25 600,130 1200,20 1200,150 0,150" fill="#050505"/>
  <polygon points="0,25 600,130 1200,20 1200,48 600,150 0,60" fill="#e3141b"/>
  <rect x="590" y="32" width="20" height="30" rx="10" fill="none" stroke="#ddd" stroke-width="2"/>
  <rect x="598" y="39" width="4" height="8" rx="2" fill="#ddd"/>
  <path d="M594 70l6 6 6-6M594 78l6 6 6-6" stroke="#ddd" stroke-width="2" fill="none"/>
</svg>

<!-- ABOUT -->
<div class="abs about-accent"></div>
<div class="photo about-photo" role="img" aria-label="Technician working beneath a lifted vehicle with exposed transmission"></div>
<div class="photo engine-art" role="img" aria-label="Wireframe illustration of an engine"></div>
<div class="abs years"><b>20</b><span>Years of<br>Experience</span></div>
<div class="abs about-side"></div>
<div class="abs eyebrow" style="left:609px;top:855px">Our Company</div>
<h2 class="abs head about-title">About Corvan</h2>
<div class="abs about-mark"></div>
<p class="abs lead">Corvan Automotive is a locally owned and operated auto repair shop in Brookfield that offers comprehensive car care and services for Navoro &amp; Omvar and all other Asian imports vehicles.</p>
<p class="abs about-copy">Led by an MTC master certified technician with 20 years experience working for Navoro &amp; Omvar dealerships, our auto shop is your go to facility for everything from factory auto maintenance, including oil changes, fluid services and tune ups, to complex engine repairs, hybrid diagnostic &amp; repair, brake jobs, etc. We have state of the art equipment and tools to ensure that we can properly diagnose and repair your vehicle to get you back on the road quickly. Our work comes with a warranty and we offer towing if needed. We also offer discounts for Ridely &amp; Zipcab rides.</p>
<div class="outline-btn">LEARN MORE</div>

<!-- PARTNERS + SERVICES -->
<div class="abs services-bg"></div>
<div class="abs partners"></div>
<div class="abs corner-tl"></div>
<div class="abs corner-br"></div>
<h3 class="abs head partners-title">Authorized installer for Veltrax oil,<br>Stateline Battery</h3>
<div class="badge" style="left:224px;top:1460px;width:82px;height:112px;background:#f2f2f2;border-radius:4px"></div>
<div class="badge" style="left:412px;top:1472px;width:104px;height:104px;border-radius:50%;border:3px solid #2b6fa3"></div>
<div class="badge" style="left:609px;top:1478px;width:140px;height:80px;background:var(--red);border-radius:6px"></div>
<div class="badge" style="left:822px;top:1497px;width:174px;height:40px;background:var(--red);transform:skewX(-15deg)"></div>

<div class="abs eyebrow svc-eyebrow">What we do</div>
<h2 class="abs head svc-title">Services Provide</h2>
<div class="abs svc-hl"></div>

<svg width="0" height="0" style="position:absolute">
  <defs><symbol id="ico" viewBox="0 0 30 30"><circle cx="15" cy="15" r="11" fill="none" stroke="#fff" stroke-width="2"/><circle cx="15" cy="15" r="4" fill="#fff"/></symbol></defs>
</svg>

<div class="svc" style="left:120px;top:1805px"><svg width="30" height="30"><use href="#ico"/></svg>Oil Changes</div>
<div class="svc" style="left:120px;top:1852px"><svg width="30" height="30"><use href="#ico"/></svg>Computer Diagnostics</div>
<div class="svc" style="left:120px;top:1898px"><svg width="30" height="30"><use href="#ico"/></svg>Electrical Specialists</div>
<div class="svc" style="left:120px;top:1945px"><svg width="30" height="30"><use href="#ico"/></svg>Tires</div>
<div class="svc" style="left:120px;top:1991px"><svg width="30" height="30"><use href="#ico"/></svg>Tire Balance &amp; Rotations</div>
<div class="svc" style="left:120px;top:2036px"><svg width="30" height="30"><use href="#ico"/></svg>Pre Purchase Inspections</div>
<div class="svc" style="left:120px;top:2083px"><svg width="30" height="30"><use href="#ico"/></svg>Insurance Claims</div>
<div class="svc" style="left:120px;top:2129px"><svg width="30" height="30"><use href="#ico"/></svg>Emission Repair &amp; Catalytic<br>Converters</div>

<div class="svc" style="left:428px;top:1805px"><svg width="30" height="30"><use href="#ico"/></svg>Engine Repair</div>
<div class="svc" style="left:428px;top:1852px"><svg width="30" height="30"><use href="#ico"/></svg>Heating &amp; AC Repair</div>
<div class="svc" style="left:428px;top:1898px"><svg width="30" height="30"><use href="#ico"/></svg>State Inspection</div>
<div class="svc" style="left:428px;top:1945px"><svg width="30" height="30"><use href="#ico"/></svg>Suspension Service &amp; Repair</div>
<div class="svc" style="left:428px;top:1991px"><svg width="30" height="30"><use href="#ico"/></svg>Leveling Kits &amp; Minor Lift Kit installation</div>
<div class="svc" style="left:428px;top:2036px"><svg width="30" height="30"><use href="#ico"/></svg>Brakes Service &amp; Repair</div>
<div class="svc" style="left:428px;top:2083px"><svg width="30" height="30"><use href="#ico"/></svg>Exhaust, Muffler Service &amp; Repair</div>
<div class="svc" style="left:428px;top:2129px"><svg width="30" height="30"><use href="#ico"/></svg>Automatic, Manual, Computerized<br>Transmission Service &amp; Repair</div>

<div class="svc" style="left:790px;top:1805px"><svg width="30" height="30"><use href="#ico"/></svg>Clutch Service &amp; Repair</div>
<div class="svc" style="left:790px;top:1852px"><svg width="30" height="30"><use href="#ico"/></svg>CV Axle Service &amp; Repair</div>
<div class="svc" style="left:790px;top:1898px"><svg width="30" height="30"><use href="#ico"/></svg>Fuel Injection System Service<br>Cleaning &amp; Repair</div>
<div class="svc" style="left:790px;top:1968px"><svg width="30" height="30"><use href="#ico"/></svg>Timing Belts &amp; Water Pumps</div>
<div class="svc" style="left:790px;top:2013px"><svg width="30" height="30"><use href="#ico"/></svg>Radiators &amp; Fans Service &amp; Repair</div>
<div class="svc" style="left:790px;top:2059px"><svg width="30" height="30"><use href="#ico"/></svg>Tune ups &amp; Factory Scheduled<br>Maintenance</div>
<div class="svc" style="left:790px;top:2129px"><svg width="30" height="30"><use href="#ico"/></svg>Hybrid Vehicle diagnostic &amp; repair<br>24-hr Night Drop</div>

<!-- GALLERY -->
<div class="abs gallery-bg"></div>
<svg class="abs" style="left:0;top:2221px" width="1200" height="145" viewBox="0 0 1200 145">
  <polygon points="0,0 1200,0 600,110" fill="#1c1c1c"/>
  <polygon points="0,0 600,110 1200,0 1200,30 600,143 0,30" fill="#6d6d6d"/>
</svg>
<div class="abs eyebrow gal-eyebrow">Photo Gallery</div>
<h2 class="abs head gal-title">Our Gallery</h2>
<div class="photo" style="left:107px;top:2513px;width:325px;height:238px;background:
  radial-gradient(ellipse 70px 60px at 80px 200px,rgba(210,170,40,.75),rgba(210,170,40,0)),
  radial-gradient(ellipse 120px 90px at 200px 110px,#222,rgba(34,34,34,0)),
  radial-gradient(ellipse 110px 80px at 60px 60px,#d8d8d4,rgba(200,200,195,0)),
  linear-gradient(140deg,#9a9a96,#5a5a58 45%,#2a2a28)" role="img" aria-label="Mechanic repairing a vehicle underside"></div>
<div class="photo" style="left:442px;top:2513px;width:323px;height:238px;background:
  radial-gradient(ellipse 50px 40px at 170px 130px,rgba(210,30,30,.85),rgba(210,30,30,0)),
  radial-gradient(ellipse 40px 90px at 230px 60px,rgba(70,120,200,.7),rgba(70,120,200,0)),
  radial-gradient(ellipse 150px 60px at 160px 200px,#0f0f10,rgba(15,15,16,0)),
  radial-gradient(ellipse 160px 80px at 160px 40px,#b9bbbf,rgba(140,142,146,0)),
  linear-gradient(160deg,#7b7d80,#3a3b3d 55%,#151516)" role="img" aria-label="Open hood of a luxury SUV with diagnostic tools"></div>
<div class="photo" style="left:777px;top:2513px;width:323px;height:238px;background:
  radial-gradient(ellipse 60px 50px at 250px 120px,rgba(220,90,40,.75),rgba(220,90,40,0)),
  radial-gradient(ellipse 110px 90px at 130px 130px,#b8bcc4,rgba(150,155,165,0)),
  radial-gradient(ellipse 120px 70px at 160px 20px,rgba(60,90,170,.9),rgba(60,90,170,0)),
  linear-gradient(150deg,#4a5a8a,#33363f 50%,#222)" role="img" aria-label="Engine bay with components removed for repair"></div>
<div class="photo" style="left:109px;top:2769px;width:487px;height:236px;background:
  radial-gradient(ellipse 60px 120px at 280px 120px,rgba(40,80,200,.95),rgba(40,80,200,0)),
  radial-gradient(ellipse 80px 70px at 120px 160px,#2a2a2a,rgba(42,42,42,0)),
  radial-gradient(ellipse 200px 80px at 200px 70px,#c9cbcf,rgba(170,172,176,0)),
  linear-gradient(170deg,#8f9195,#6a6c70 50%,#3e3f43)" role="img" aria-label="Pickup truck on a lift with wheel removed"></div>
<div class="photo" style="left:612px;top:2769px;width:488px;height:236px;background:
  radial-gradient(ellipse 240px 50px at 244px 170px,#1d1d1d,rgba(29,29,29,0)),
  radial-gradient(ellipse 40px 30px at 270px 30px,rgba(200,40,40,.7),rgba(200,40,40,0)),
  linear-gradient(180deg,#e2e3df 0%,#c7c8c3 35%,#6b6b68 62%,#8a8a86 85%,#5a5a58 100%)" role="img" aria-label="Row of SUVs parked in front of the repair shop"></div>

<!-- MAKES -->
<h3 class="abs head makes-title">Corvan Automotive specializes in Navoro &amp; Omvar<br>auto repair but also service and repair<br>the following makes</h3>
<div class="abs makes">
  <div class="make"><i></i>Aceron</div>
  <div class="make"><i></i>Haelan</div>
  <div class="make"><i></i>Ivora</div>
  <div class="make"><i></i>Kessa</div>
  <div class="make silver"><i></i>Mirano</div>
  <div class="make"><i></i>Soren</div>
  <div class="make"><i></i>Tavren</div>
  <div class="make"><i></i>Hoshiro</div>
</div>
<div class="btn" style="left:444px;top:3607px;width:292px;height:57px">Schedule an appointment</div>

<!-- CONTACT -->
<div class="abs contact-bg"></div>
<div class="abs contact-line"></div>
<div class="abs eyebrow contact-eyebrow">Get in touch</div>
<h2 class="abs head contact-title">Contact <span>Us</span></h2>
<p class="abs contact-copy">Contact us for a free estimate! Please include year, make, and model and the service or repair you would like repair you would like an estimate on.</p>
<div class="btn" style="left:140px;top:4087px;width:234px;height:45px;font-size:13px">Schedule an appointment</div>
<div class="pay"><i></i>paysmooth <small style="font-size:14px;font-weight:400;color:#999">finance</small></div>

<div class="abs form"></div>
<h3 class="abs head form-title">Leave us a message</h3>
<div class="field" style="left:636px;top:3915px;width:200px;height:38px">First Name*</div>
<div class="field" style="left:847px;top:3915px;width:201px;height:38px">Last Name*</div>
<div class="field" style="left:636px;top:3963px;width:200px;height:40px">Email address*</div>
<div class="field" style="left:847px;top:3963px;width:201px;height:40px">Phone*</div>
<div class="field" style="left:636px;top:4015px;width:412px;height:79px">Message</div>
<div class="btn" style="left:638px;top:4112px;width:130px;height:36px;font-family:var(--head);font-size:12px;letter-spacing:1px">Submit</div>

<!-- FOOTER -->
<svg class="abs" style="left:0;top:4307px" width="1200" height="110" viewBox="0 0 1200 110">
  <polygon points="0,55 500,25 500,42 0,75" fill="#e3141b"/>
  <polygon points="1200,55 700,25 700,42 1200,75" fill="#e3141b"/>
</svg>
<div class="brand" style="left:536px;top:4342px;font-size:26px"><span class="dot"></span>Corvan</div>
<nav class="footer-nav">
  <a style="left:247px">Home</a><span class="dot" style="left:330px"></span>
  <a style="left:373px">About Us</a><span class="dot" style="left:490px"></span>
  <a style="left:532px">Our Services</a><span class="dot" style="left:685px"></span>
  <a style="left:725px">Gallery</a><span class="dot" style="left:838px"></span>
  <a style="left:878px">Contact</a>
</nav>
<p class="abs copyright">Copyright © 2024 Corvan Automotive. All rights reserved.</p>
<div class="social"><span>Forum</span><span>Chirp</span><span>Proline</span><span>Snapgrid</span></div>

</body>
</html>
```